Veltrane Group Business Card Design

The CEO is looking for a new trendy look for his business card.
You can stay with current branding or come up with something new/creative. It can be 3D, including Medical Office buildings. You can use our logo in a variety of colors. Please include name, title, company name, company website, email address, cell number

Target Market(s)

Real Estate Development and Construction

Industry/Entity Type

Health care real estate

Contact Information for Business Card

Rohesh Kamdar, CEO M-604.781.2249 E-roheshkamdar@veltrane.com Address:4180 Lindqvist Ave, Tampa, FL 33482 www.veltrane.com

Font styles to use
Other font styles liked:
• Be creative

Requirements
Must have
• Creative, trendy look
Nice to have
• Please go to our website to get a feel- www. veltrane.com
Should not have
• small fonts

```html
<!DOCTYPE html>
<html lang="en">
<head>
<meta charset="utf-8">
<title>Veltrane Group Business Card</title>
<link rel="stylesheet" href="https://fonts.googleapis.com/css2?family=Lato:wght@400;700;900&display=swap">
<style>
  :root {
    --stage: #3a3a3c;
    --navy: #1f3152;
    --red: #b21e2a;
    --red-deep: #8e1620;
    --red-light: #d22a35;
    --white: #ffffff;
  }
  * { margin: 0; padding: 0; box-sizing: border-box; }
  html, body { width: 1200px; height: 689px; overflow: hidden; }
  body {
    background: var(--stage);
    font-family: "Lato", sans-serif;
    position: relative;
  }
  .card {
    position: absolute;
    top: 196px;
    width: 520px;
    height: 297px;
    border-radius: 18px;
    overflow: hidden;
  }
  .card-back {
    left: 50px;
    background: linear-gradient(135deg, var(--red-light) 0%, var(--red) 50%, var(--red-deep) 100%);
  }
  .card-back .pattern-area {
    position: absolute; inset: 0;
    background: linear-gradient(135deg, rgba(255,255,255,0.06), rgba(0,0,0,0.08));
  }
  .card-back .wordmark {
    position: absolute;
    right: 34px;
    bottom: 30px;
    color: var(--white);
    font-weight: 900;
    font-size: 30px;
    letter-spacing: -0.5px;
  }
  .card-front {
    left: 630px;
    background: var(--navy);
  }
  .card-front .wordmark {
    position: absolute;
    left: 0; right: 0;
    top: 22px;
    text-align: center;
    color: var(--red);
    font-weight: 900;
    font-size: 70px;
    line-height: 1;
    letter-spacing: -2px;
  }
  .info-band {
    position: absolute;
    left: 0; right: 0;
    top: 112px;
    height: 124px;
    background: var(--white);
    display: flex;
    align-items: center;
    padding: 0 22px 0 26px;
  }
  .identity { flex: 0 0 auto; }
  .person-name {
    color: var(--red);
    font-weight: 900;
    font-size: 25px;
    letter-spacing: 0.5px;
    line-height: 1.1;
  }
  .person-title {
    color: var(--navy);
    font-size: 16px;
    margin-top: 4px;
    text-align: right;
  }
  .divider {
    width: 2px;
    height: 70px;
    background: var(--red);
    margin: 0 14px;
    flex: 0 0 auto;
  }
  .contacts { list-style: none; }
  .contacts li {
    display: flex;
    align-items: center;
    gap: 7px;
    color: var(--navy);
    font-size: 13px;
    line-height: 1.75;
    white-space: nowrap;
  }
  .contacts svg, .address svg { flex: 0 0 auto; }
  .address {
    position: absolute;
    left: 0; right: 0;
    top: 250px;
    display: flex;
    justify-content: center;
    align-items: center;
    gap: 7px;
    color: var(--white);
    font-size: 15px;
    letter-spacing: 0.2px;
  }
</style>
</head>
<body>
  <section class="card card-back">
    <div class="pattern-area" role="img" aria-label="Embossed repeating company name pattern in deep red"></div>
    <div class="wordmark">Veltrane</div>
  </section>

  <section class="card card-front">
    <div class="wordmark">Veltrane</div>
    <div class="info-band">
      <div class="identity">
        <div class="person-name">ROHESH KAMDAR</div>
        <div class="person-title">President / CEO</div>
      </div>
      <div class="divider"></div>
      <ul class="contacts">
        <li>
          <svg width="11" height="13" viewBox="0 0 11 13"><rect x="1.5" y="0.8" width="8" height="11.4" rx="1.6" fill="none" stroke="#b21e2a" stroke-width="1.6"/><circle cx="5.5" cy="10" r="0.9" fill="#b21e2a"/></svg>
          604.781.2249
        </li>
        <li>
          <svg width="13" height="10" viewBox="0 0 13 10"><rect x="0" y="0" width="13" height="10" rx="1" fill="#b21e2a"/><path d="M0.8 1 L6.5 5.6 L12.2 1" fill="none" stroke="#fff" stroke-width="1.2"/></svg>
          roheshkamdar@veltrane.com
        </li>
        <li>
          <svg width="13" height="13" viewBox="0 0 13 13"><circle cx="6.5" cy="6.5" r="5.7" fill="none" stroke="#b21e2a" stroke-width="1.4"/><ellipse cx="6.5" cy="6.5" rx="2.4" ry="5.7" fill="none" stroke="#b21e2a" stroke-width="1.1"/><line x1="0.8" y1="6.5" x2="12.2" y2="6.5" stroke="#b21e2a" stroke-width="1.1"/></svg>
          www.veltrane.com
        </li>
      </ul>
    </div>
    <div class="address">
      <svg width="11" height="15" viewBox="0 0 11 15"><path d="M5.5 0.5 A5 5 0 0 1 10.5 5.5 C10.5 9 5.5 14.5 5.5 14.5 C5.5 14.5 0.5 9 0.5 5.5 A5 5 0 0 1 5.5 0.5 Z" fill="#b21e2a"/><circle cx="5.5" cy="5.4" r="1.9" fill="#1f3152"/></svg>
      4180 Lindqvist Ave, Suite 260 Tampa, FL 33482
    </div>
  </section>
</body>
</html>
```